Simple, 1-Page Project - Life-saving Pulsekeep Devices

We recently kicked off a project to bring all geographic location records for automatic emergency defibrillators (AEDs) in the State of New York online (instead of kept in paper in drawers). This hope is that is will ultimately save thousands of lives, as 9-1-1 operators will be able to quickly direct civilians to the nearest AED to bring to people suffering a cardiac event (e.g., a heart attack).

This page will be used to describe this effort, our progress thus far and how far we have left to go.

I am looking for a 1-page design - coded for both a responsive version for mobile devices and a traditional version - that would ***ideally*** plug into my existing WordPress site (https://qv-lmt.org), but it's not a requirement.

Target Market(s)

General public (non-physicians/non-EMTs)

Requirements
Must have
• - Our logo (please note, our logo is the Birchfield Vale Chapter logo...attached)
Nice to have
• - Would be wonderful to have an area with a clickable map showing where the participating regions are - which, once clicked, will take to you their specific sites. Regions are large chunks of land encompassing multiple towns, NOT a singular, specific place A nice-looking Google Map, a la Plumtail Grids (https://plumtailgrids.com/) would be cool if this were possible..
• - If you need a headline or page title, you can use: "Bringing AEDs in New York Online"
• - Would be nice if the design incorporated the color scheme of our brand (see attachment) and/or our main website: https://qv-lmt.org/
• - Would be nice to have some AED imagery - I attached some common symbols seen in AED advertising for inspiration
Should not have
• - This is a serious topic, so the design should be respectful and not too silly/cartoonish
• - Stock images, if chosen, should be thoughtful and classy

```html
<!DOCTYPE html>
<html lang="en">
<head>
<meta charset="utf-8">
<title>Bringing AEDs in New York Online</title>
<link rel="stylesheet" href="https://fonts.googleapis.com/css2?family=Libre+Baskerville:wght@400;700&family=Roboto:wght@400;500;700;900&display=swap">
<style>
:root{
  --navy:#0f2b5d;
  --navy-deep:#0b224c;
  --gold:#a39a6e;
  --gold-dark:#8f875c;
  --red:#d3212b;
  --ink:#222;
  --muted:#666;
  --paper:#f4f3f1;
  --white:#fff;
}
*{box-sizing:border-box;margin:0;padding:0}
html,body{width:1200px;height:3238px;overflow:hidden}
body{position:relative;font-family:'Roboto',sans-serif;color:var(--ink);background:var(--paper)}
.abs{position:absolute}
.serif{font-family:'Libre Baskerville',serif;font-weight:700}

/* header */
.site-header{position:absolute;left:0;top:0;width:1200px;height:94px;background:var(--white);border-top:3px solid var(--gold);z-index:5}
.brand{position:absolute;left:146px;top:8px;display:flex;align-items:center;gap:16px}
.brand-mark{width:80px;height:80px;border-radius:50%;background:var(--navy)}
.brand-name{font-family:'Libre Baskerville',serif;font-weight:400;font-size:24px;color:var(--navy);line-height:1.15;width:200px}
.main-nav{position:absolute;right:144px;top:38px;display:flex;gap:33px}
.main-nav a{font-size:14px;font-weight:500;color:#222;text-decoration:none;letter-spacing:.2px}

/* hero */
.hero-art{position:absolute;left:0;top:94px;z-index:1}
.hero-title{position:absolute;left:0;top:280px;width:1200px;text-align:center;color:var(--white);font-size:60px;line-height:66px;text-shadow:0 2px 6px rgba(0,0,0,.5);z-index:2}
.hero-sub{position:absolute;left:0;top:436px;width:1200px;text-align:center;color:var(--white);font-size:22px;font-weight:500;z-index:2}
.btn{position:absolute;display:flex;align-items:center;justify-content:center;gap:8px;border-radius:30px;color:var(--white);font-weight:500;text-decoration:none;z-index:2}
.btn-gold{background:var(--gold)}
.btn-navy{background:var(--navy-deep)}
.btn .arrow{width:15px;height:15px;border-radius:50%;background:var(--white);display:inline-flex;align-items:center;justify-content:center}
.dots{position:absolute;left:556px;top:685px;display:flex;gap:9px;z-index:2}
.dots span{width:10px;height:10px;border-radius:50%;background:var(--white)}
.dots span.on{background:transparent;border:2px solid var(--white)}

/* welcome */
.welcome-bg{position:absolute;left:0;top:700px;width:1200px;height:1300px;background:linear-gradient(160deg,#ebe9e6,#f7f6f4 40%,#e6e4e0)}
.ghost{position:absolute;font-weight:900;color:rgba(0,0,0,.06);font-size:100px;letter-spacing:2px;white-space:nowrap}
.ghost-v{transform:rotate(-90deg);transform-origin:left top}
.welcome-title{position:absolute;right:597px;top:848px;font-size:36px;color:#111}
.welcome-text{position:absolute;left:150px;top:915px;width:453px;text-align:right;font-size:13.5px;line-height:30.3px;color:#555}
.welcome-photo{position:absolute;left:667px;top:820px;width:382px;height:382px;border-radius:50%;border:5px solid var(--navy);padding:6px;background:var(--white)}
.welcome-photo div{width:100%;height:100%;border-radius:50%;background:linear-gradient(150deg,#d9d6cf,#b9b6ae 45%,#3b4a6a)}

/* provide */
.provide-band{position:absolute;left:0;top:1260px;z-index:1}
.provide-title{position:absolute;left:0;top:1378px;width:1200px;text-align:center;color:var(--white);font-size:36px;z-index:2}
.feature{position:absolute;width:300px;color:var(--white);z-index:2}
.feature h3{font-size:15.5px;font-weight:500;letter-spacing:.3px;margin-bottom:14px}
.feature p{font-size:12.5px;line-height:21.5px;color:#e4e8f0}
.feature.left{text-align:right;left:140px}
.feature.right{left:759px}
.feature-icon{position:absolute;width:96px;height:96px;border-radius:50%;background:var(--white);display:flex;align-items:center;justify-content:center;z-index:2}

/* blog */
.blog-title{position:absolute;left:0;top:1912px;width:1200px;text-align:center;font-size:36px;color:#111}
.post{position:absolute;top:1995px;width:279px;height:345px;background:var(--white);box-shadow:0 2px 10px rgba(0,0,0,.08)}
.post-img{height:163px}
.post-date{position:absolute;left:23px;top:179px;width:47px;height:48px;color:var(--white);text-align:center;font-size:15px;line-height:19px;padding-top:5px;font-weight:500}
.post h4{position:absolute;left:84px;top:181px;font-size:15px;font-weight:500;line-height:21px;color:#111}
.post p{position:absolute;left:23px;top:247px;width:240px;font-size:12px;line-height:19px;color:#888}
.post a{position:absolute;left:23px;top:315px;font-size:12.5px;font-weight:500;color:var(--gold);text-decoration:none}

/* contact */
.map{position:absolute;left:0;top:2429px;width:600px;height:465px;background:linear-gradient(135deg,#d7dcd9,#c9d0cd 50%,#dfe3e0)}
.contact-panel{position:absolute;left:600px;top:2429px;width:600px;height:465px;background:var(--gold);overflow:hidden}
.contact-title{position:absolute;left:657px;top:2502px;font-size:34px;color:var(--white)}
.field{position:absolute;background:var(--white);font-size:12px;color:#888;padding:13px 17px}
.heart-badge{position:absolute;left:537px;top:2605px;width:110px;height:110px;border-radius:50%;background:var(--gold);display:flex;align-items:center;justify-content:center;z-index:3}

/* footer */
.site-footer{position:absolute;left:0;top:2894px;width:1200px;height:344px;background:var(--navy)}
.foot-brand{position:absolute;left:170px;top:2953px;display:flex;align-items:center;gap:16px}
.foot-brand .brand-mark{background:var(--white)}
.foot-brand .brand-name{color:var(--white);font-size:26px;width:220px}
.social{position:absolute;left:170px;top:3057px;display:flex;gap:9px}
.social span{width:34px;height:34px;border-radius:50%;border:1.5px solid var(--white)}
.foot-h{position:absolute;top:2952px;color:var(--white);font-size:15px;font-weight:500;letter-spacing:.3px}
.foot-text{position:absolute;color:#dfe4ee;font-size:11.5px;line-height:19px}
.news-input{position:absolute;left:535px;top:3038px;width:240px;height:38px;background:var(--white);font-size:11px;color:#777;padding:12px 13px}
.news-btn{position:absolute;left:535px;top:3086px;width:113px;height:34px;background:var(--gold);color:var(--white);font-size:11.5px;font-weight:500;display:flex;align-items:center;justify-content:center}
.contact-row{position:absolute;left:848px;display:flex;gap:10px;color:#dfe4ee;font-size:11.5px;line-height:19px;width:200px}
.copyright{position:absolute;left:0;top:3198px;width:1200px;text-align:center;color:#dfe4ee;font-size:12px}
.to-top{position:absolute;left:971px;top:3189px;width:46px;height:35px;background:var(--gold);display:flex;align-items:center;justify-content:center}
</style>
</head>
<body>

<header class="site-header">
  <div class="brand">
    <span class="brand-mark"></span>
    <span class="brand-name">Birchfield Vale Chapter</span>
  </div>
  <nav class="main-nav">
    <a href="#">HOME</a><a href="#">PRODUCTS</a><a href="#">RESOURCES</a><a href="#">NEWS &amp; EVENTS</a><a href="#">ABOUT US</a>
  </nav>
</header>

<svg class="hero-art" width="1200" height="680" viewBox="0 94 1200 680" role="img" aria-label="Evening aerial view of the New York City skyline with lit towers and the river">
  <defs>
    <linearGradient id="heroSky" x1="0" y1="0" x2="0" y2="1">
      <stop offset="0" stop-color="#1b2b4a"/>
      <stop offset=".45" stop-color="#4a4c5c"/>
      <stop offset=".75" stop-color="#6b5638"/>
      <stop offset="1" stop-color="#2a2d38"/>
    </linearGradient>
  </defs>
  <path d="M0 94H1200V628Q600 880 0 628Z" fill="url(#heroSky)"/>
  <path d="M0 628Q600 880 1200 628Q600 905 0 628Z" fill="#0f2b5d"/>
</svg>
<h1 class="hero-title serif">BRINGING AEDS<br>IN NEW YORK ONLINE</h1>
<p class="hero-sub">Lorem ipsum dolor sit amet consectetur adipiscing elit</p>
<a class="btn btn-gold" href="#" style="left:506px;top:503px;width:188px;height:56px;font-size:17px">GET STARTED
  <span class="arrow"><svg width="9" height="9" viewBox="0 0 10 10"><path d="M2 5h6M5 2l3 3-3 3" stroke="#a39a6e" stroke-width="1.8" fill="none"/></svg></span></a>
<div class="dots"><span></span><span></span><span class="on"></span><span></span><span></span></div>

<section>
  <div class="welcome-bg" role="img" aria-label="Faded photo of a rescuer using an AED"></div>
  <div class="ghost ghost-v" style="left:30px;top:1245px">WELCOME</div>
  <h2 class="welcome-title serif">WELCOME</h2>
  <p class="welcome-text">Lorem ipsum dolor sit amet, consectetur adipiscing elit, sed do eiusmod tempor incididunt ut labore et dolore magna aliqua. Ut enim ad minim veniam, quis nostrud exercitation ullamco laboris nisi ut aliquip ex ea commodo consequat. Duis aute irure dolor in reprehenderit in voluptate velit esse cillum dolore eu fugiat nulla pariatur. Excepteur sint occaecat cupidatat non proident, sunt in culpa qui officia deserunt mollit anim id est laborum</p>
  <a class="btn btn-gold" href="#" style="left:429px;top:1127px;width:174px;height:45px;font-size:16px">MORE INFO
    <span class="arrow"><svg width="9" height="9" viewBox="0 0 10 10"><path d="M2 5h6M5 2l3 3-3 3" stroke="#a39a6e" stroke-width="1.8" fill="none"/></svg></span></a>
  <div class="welcome-photo"><div role="img" aria-label="Woman kneeling beside a collapsed man, using an AED"></div></div>
</section>

<section>
  <svg class="provide-band" width="1200" height="600" viewBox="0 1260 1200 600">
    <path d="M0 1370Q600 1180 1200 1370V1740Q600 1930 0 1740Z" fill="#0f2b5d"/>
    <path d="M0 1370Q600 1180 1200 1370Q600 1170 0 1360Z" fill="#a39a6e"/>
    <path d="M0 1740Q600 1930 1200 1740Q600 1942 0 1752Z" fill="#a39a6e"/>
  </svg>
  <div class="ghost" style="left:952px;top:1350px;color:rgba(255,255,255,.12);z-index:2">SERV</div>
  <h2 class="provide-title serif">WHAT WE PROVIDE</h2>

  <div class="feature left" style="top:1476px;width:300px"><h3>OCCAECAT CUPIDATAT</h3><p>Lorem ipsum dolor sit ameconsectetur adipiscing elit, sed do eiusmod tempor incididunt ut labore et dolore magna aliquenim ad minim veniam,</p></div>
  <div class="feature left" style="top:1614px;width:300px"><h3>DUIS AUTE IRURE</h3><p>Lorem ipsum dolor sit ameconsectetur adipiscing elit, sed do eiusmod tempor incididunt ut labore et dolore magna aliquenim ad minim veniam,</p></div>
  <div class="feature right" style="top:1476px"><h3>INCIDIDUNT UT LAB</h3><p>Lorem ipsum dolor sit ameconsectetur adipiscing elit, sed do eiusmod tempor incididunt ut labore et dolore magna aliquenim ad minim veniam,</p></div>
  <div class="feature right" style="top:1614px"><h3>EXERCITATION ULLAMC</h3><p>Lorem ipsum dolor sit ameconsectetur adipiscing elit, sed do eiusmod tempor incididunt ut labore et dolore magna aliquenim ad minim veniam,</p></div>

  <div class="feature-icon" style="left:458px;top:1479px"><svg width="54" height="50" viewBox="0 0 54 50" fill="none" stroke="#0f2b5d" stroke-width="2.4"><path d="M27 46C10 33 3 25 3 15 3 8 9 3 15 3c5 0 9 3 12 7 3-4 7-7 12-7 6 0 12 5 12 12 0 10-7 18-24 31Z"/><path d="M9 24h10l4-7 5 13 4-6h13"/></svg></div>
  <div class="feature-icon" style="left:643px;top:1479px"><svg width="56" height="46" viewBox="0 0 56 46" fill="none" stroke="#0f2b5d" stroke-width="2.4"><circle cx="28" cy="12" r="6"/><circle cx="11" cy="17" r="5"/><circle cx="45" cy="17" r="5"/><path d="M17 44V30c0-6 5-9 11-9s11 3 11 9v14M2 42V32c0-5 4-7 9-7M54 42V32c0-5-4-7-9-7"/></svg></div>
  <div class="feature-icon" style="left:458px;top:1617px"><svg width="50" height="50" viewBox="0 0 50 50" fill="none" stroke="#0f2b5d" stroke-width="2.4"><circle cx="25" cy="18" r="10"/><path d="M12 18a13 13 0 0 1 26 0M12 16v6M38 16v6M38 22c0 4-4 6-9 6"/><path d="M6 48c0-10 8-16 19-16s19 6 19 16Z"/></svg></div>
  <div class="feature-icon" style="left:643px;top:1617px"><svg width="54" height="48" viewBox="0 0 54 48" fill="none" stroke="#0f2b5d" stroke-width="2.4"><rect x="3" y="3" width="38" height="30" rx="2"/><path d="M7 19h8l3-6 5 11 3-5h8"/><path d="M40 45c-8-6-11-9-11-14 0-3 2-5 5-5 2 0 4 1 6 3 2-2 4-3 6-3 3 0 5 2 5 5 0 5-3 8-11 14Z"/></svg></div>

  <svg class="abs" style="left:560px;top:1568px;z-index:3" width="80" height="72" viewBox="0 0 80 72" role="img" aria-label="AED heart symbol"><path d="M40 70C14 50 2 38 2 22 2 11 11 2 22 2c8 0 14 4 18 10 4-6 10-10 18-10 11 0 20 9 20 20 0 16-12 28-38 48Z" fill="#d3212b"/><path d="M45 12 30 38h10l-6 22 17-29H40Z" fill="#fff"/></svg>
</section>

<section>
  <div class="ghost ghost-v" style="left:1088px;top:2410px">BLOG POSTS</div>
  <h2 class="blog-title serif">BLOG POSTS</h2>

  <article class="post" style="left:144px">
    <div class="post-img" role="img" aria-label="Gloved hands placing AED pads on a patient" style="background:linear-gradient(135deg,#8aa84a,#b9ada0 45%,#4e4440)"></div>
    <div class="post-date" style="background:var(--navy)">12<br>JAN</div>
    <h4>Pellentesque faucibus<br>Ut accumsan ultric</h4>
    <p>Duis quam Nam eget lacus Aliquam erat volutpat Quisque dignissim congue leo Mauris vel la vestibulum</p>
    <a href="#">READ MORE</a>
  </article>
  <article class="post" style="left:461px">
    <div class="post-img" role="img" aria-label="Open AED unit with electrode pads" style="background:linear-gradient(135deg,#3d3a30,#c3604f 50%,#524b3e)"></div>
    <div class="post-date" style="background:var(--gold)">12<br>JAN</div>
    <h4>Pellentesque faucibus<br>Ut accumsan ultric</h4>
    <p>Duis quam Nam eget lacus Aliquam erat volutpat Quisque dignissim congue leo Mauris vel la vestibulum</p>
    <a href="#">READ MORE</a>
  </article>
  <article class="post" style="left:778px">
    <div class="post-img" role="img" aria-label="Rescuers performing CPR with an AED" style="background:linear-gradient(135deg,#5a5650,#c9c4bc 45%,#2c4f8c)"></div>
    <div class="post-date" style="background:var(--navy)">12<br>JAN</div>
    <h4>Pellentesque faucibus<br>Ut accumsan ultric</h4>
    <p>Duis quam Nam eget lacus Aliquam erat volutpat Quisque dignissim congue leo Mauris vel la vestibulum</p>
    <a href="#">READ MORE</a>
  </article>
</section>

<section>
  <div class="map" role="img" aria-label="Street map of New York City and surrounding boroughs with location pins"></div>
  <div class="contact-panel"><div class="ghost" style="left:295px;top:355px;color:rgba(0,0,0,.07)">CONTA</div></div>
  <div class="heart-badge"><svg width="74" height="66" viewBox="0 0 80 72" role="img" aria-label="AED heart symbol"><path d="M40 70C14 50 2 38 2 22 2 11 11 2 22 2c8 0 14 4 18 10 4-6 10-10 18-10 11 0 20 9 20 20 0 16-12 28-38 48Z" fill="#d3212b"/><path d="M45 12 30 38h10l-6 22 17-29H40Z" fill="#fff"/></svg></div>
  <h2 class="contact-title serif">GET IN TOUCH</h2>
  <div class="field" style="left:657px;top:2570px;width:192px;height:40px">Enter Name</div>
  <div class="field" style="left:862px;top:2570px;width:192px;height:40px">Enter Email</div>
  <div class="field" style="left:657px;top:2620px;width:192px;height:40px">Phone</div>
  <div class="field" style="left:862px;top:2620px;width:192px;height:40px">Address</div>
  <div class="field" style="left:657px;top:2670px;width:397px;height:70px">Message</div>
  <a class="btn btn-navy" href="#" style="left:657px;top:2768px;width:232px;height:49px;font-size:17px">SUBMIT MESSAGE
    <span class="arrow"><svg width="9" height="9" viewBox="0 0 10 10"><path d="M2 5h6M5 2l3 3-3 3" stroke="#0b224c" stroke-width="1.8" fill="none"/></svg></span></a>
</section>

<footer class="site-footer"></footer>
<div class="foot-brand">
  <span class="brand-mark" style="width:82px;height:82px"></span>
  <span class="brand-name">Birchfield Vale Chapter</span>
</div>
<div class="social" aria-label="Social links"><span></span><span></span><span></span><span></span></div>

<h3 class="foot-h" style="left:535px">SIGN UP FOR NEWSLETTER</h3>
<p class="foot-text" style="left:535px;top:2996px;width:200px">Excepteur sint occaecat cupidatat non proident, suntfficia deserunt</p>
<div class="news-input">Enter email</div>
<div class="news-btn">SUBSCRIPTION</div>

<h3 class="foot-h" style="left:844px">CONTACT US</h3>
<div class="contact-row" style="top:2998px"><svg width="12" height="14" viewBox="0 0 12 14"><path d="M6 13S1 8 1 5a5 5 0 0 1 10 0c0 3-5 8-5 8Z" fill="none" stroke="#a39a6e" stroke-width="1.5"/><circle cx="6" cy="5" r="1.6" fill="#a39a6e"/></svg><span>234.Sed ut perspiciatis unde omnis iste natus error sit voluptatem</span></div>
<div class="contact-row" style="top:3066px"><svg width="12" height="12" viewBox="0 0 12 12"><path d="M2 1h3l1 3-2 1a7 7 0 0 0 3 3l1-2 3 1v3c-6 0-10-4-9-9Z" fill="#a39a6e"/></svg><span>Phone:&nbsp; 1 800 555 0142</span></div>
<div class="contact-row" style="top:3094px"><svg width="12" height="10" viewBox="0 0 12 10"><rect x="1" y="1" width="10" height="8" fill="#a39a6e"/><path d="M1 1l5 4 5-4" stroke="#0f2b5d" fill="none"/></svg><span>Email: info@pulsekeep.org</span></div>

<p class="copyright">©2019 Pulsekeep Devices, All Rights Reserved &nbsp;|&nbsp; Privacy Policy</p>
<div class="to-top" aria-label="Back to top"><svg width="16" height="16" viewBox="0 0 16 16" fill="none" stroke="#fff" stroke-width="1.6"><path d="M3 8l5-5 5 5M3 13l5-5 5 5"/></svg></div>

</body>
</html>
```